Diverse, up-scale salon needs eye-catching, unique business cards.

We are looking for a unique business card design for our stylist but that can also be multi functional and used for appointment reminder and referrals. I will need a design in a format that I can modify names and titles going forward. In the past we have had a dark background with the logo on one side, and stylist and contact information on the other but we are open to all ideas. I have included our mission statement as well as branded colors below. The statement doesn't need to go on the card, it's just a reference for target market. We need space for the stylists name, title, instagram handle and then the salons phone number, website and address. I am also open to adding a spot for a qr code linked to the stylist instagram or the salon booking link.

primary brand colors:
#333333 #233415 #36502a #93874a #000000
Mission statement:
Vessolin Hair Studio, a high-end salon located in the lively Downtown Farmington, Michigan, is committed to providing exceptional services in a welcoming and relaxed environment to meet the needs of our diverse clientele.
Our salon specializes in contemporary custom haircuts, coloring, extensions, and barbering and beard grooming services. Our team of skilled stylists is passionate and inventive in their hair styling techniques. At the heart of our salon are values centered on quality, innovation, creativity, and above all, comfort. These core values are evident in every appointment across our customizable array of services.
Our goal is to establish a benchmark for exceptional hair care for every human.
Website: www.vessolinhairstudio.example
instagram: @vessolinhairstudio
address: 41782 Pelham Crest Rd, Farmington MI
phone: 248-613-4087

Industry/Entity Type

Hair Salon

Contact Information for Business Card

Stylist name, title, phone, instagram, website, address, (optional qr code)

Requirements
Should not have
• Does not need mission statement on the card.

```html
<!DOCTYPE html>
<html lang="en">
<head>
<meta charset="utf-8">
<title>Vessolin Hair Studio – Business Card</title>
<link href="https://fonts.googleapis.com/css2?family=Cinzel:wght@500&family=Montserrat:wght@400;600&display=swap" rel="stylesheet">
<style>
  :root {
    --backdrop: #3a3a3a;
    --card: #141414;
    --card-back: #111111;
    --gold: #93874a;
    --white: #f2f2f2;
    --pattern-dark: #0c0c0c;
    --pattern-light: #262626;
  }
  * { box-sizing: border-box; margin: 0; padding: 0; }
  html, body {
    width: 1200px; height: 801px; overflow: hidden;
    background: var(--backdrop);
  }
  .canvas {
    width: 1200px; height: 801px;
    display: flex; align-items: center; justify-content: center; gap: 40px;
  }
  .card {
    position: relative;
    width: 540px; height: 309px;
    border: 2px solid var(--gold);
    border-radius: 3px;
    overflow: hidden;
    font-family: "Montserrat", sans-serif;
    box-shadow: 0 18px 40px rgba(0,0,0,.35);
  }
  /* Front */
  .card-front { background: var(--card); }
  .divider {
    position: absolute; left: 30px; right: 30px; top: 170px;
    height: 1px; background: var(--gold);
  }
  .stylist { position: absolute; left: 34px; top: 108px; }
  .stylist-name {
    font-family: "Cinzel", serif; font-weight: 500;
    color: var(--gold); font-size: 24px; letter-spacing: 1px; line-height: 1;
  }
  .stylist-title { color: var(--white); font-size: 15px; margin-top: 4px; }
  .contact-list {
    position: absolute; left: 34px; top: 186px;
    list-style: none; color: var(--white); font-size: 15px;
  }
  .contact-list li { display: flex; align-items: center; gap: 9px; line-height: 27px; }
  .contact-list svg { width: 13px; height: 13px; flex: none; }
  .address {
    position: absolute; right: 34px; top: 184px;
    text-align: right; color: var(--white); font-size: 15px; line-height: 24px;
  }
  .brand-lockup {
    position: absolute; right: 30px; top: 22px;
    display: flex; align-items: center; gap: 12px;
  }
  .brand-name {
    font-family: "Montserrat", sans-serif; font-weight: 600;
    color: var(--gold); font-size: 13px; letter-spacing: 2px;
    text-align: right; line-height: 18px;
  }
  .brand-ring {
    width: 104px; height: 104px; border-radius: 50%;
    border: 3px solid var(--gold);
  }
  /* Back */
  .card-back { background: var(--card-back); }
  .pattern-field {
    position: absolute; inset: 0;
    background: linear-gradient(110deg, var(--pattern-dark) 0%, var(--card-back) 45%, var(--pattern-light) 100%);
  }
  .back-lockup {
    position: absolute; inset: 0;
    display: flex; flex-direction: column; align-items: center; justify-content: center; gap: 14px;
  }
  .back-ring {
    width: 120px; height: 120px; border-radius: 50%;
    border: 4px solid var(--gold);
  }
  .back-name {
    font-family: "Montserrat", sans-serif; font-weight: 600;
    color: var(--gold); font-size: 20px; letter-spacing: 3px;
  }
</style>
</head>
<body>
<main class="canvas">
  <section class="card card-front">
    <div class="brand-lockup">
      <p class="brand-name">VESSOLIN<br>HAIR STUDIO</p>
      <div class="brand-ring"></div>
    </div>

    <div class="stylist">
      <p class="stylist-name">MARISOL</p>
      <p class="stylist-title">President</p>
    </div>

    <div class="divider"></div>

    <ul class="contact-list">
      <li>
        <svg viewBox="0 0 16 16" aria-hidden="true"><path fill="var(--gold)" d="M3.6 1.5l2.3 2.6-1.3 1.8c.9 2 2.5 3.6 4.5 4.5l1.8-1.3 2.6 2.3-1.5 2.3C7 13.4 2.6 9 1.3 3z"/></svg>
        248-613-4087
      </li>
      <li>
        <svg viewBox="0 0 16 16" aria-hidden="true"><circle cx="8" cy="8" r="6" fill="none" stroke="var(--gold)" stroke-width="2"/></svg>
        @vessolinhairstudio
      </li>
      <li>
        <svg viewBox="0 0 16 16" aria-hidden="true"><g fill="none" stroke="var(--gold)" stroke-width="1.5"><circle cx="8" cy="8" r="6.5"/><ellipse cx="8" cy="8" rx="2.8" ry="6.5"/><path d="M1.5 8h13"/></g></svg>
        www.vessolinhairstudio.example
      </li>
    </ul>

    <p class="address">41782 Pelham Crest Rd<br>Farmington MI</p>
  </section>

  <section class="card card-back">
    <div class="pattern-field" role="img" aria-label="Tonal black repeating monogram pattern across the card"></div>
    <div class="back-lockup">
      <div class="back-ring"></div>
      <p class="back-name">VESSOLIN HAIR STUDIO</p>
    </div>
  </section>
</main>
</body>
</html>
```